Quorbelline.io - Please redesign to make it look better from current design

We already have the current website, that you can access but we think it can improve from current version.
Quorbelline is a cryptocurrency hedge fund that allow you to participate in the hedge fund with cryptocurrency such as eth.
At current phase, we are doing an ICO, then we want to make sure that the website it looks professional, beautiful and trustable enough for investors after looking at our website.
Target Market(s)
Investors
Industry/Entity Type
Investment
Coding
Coded - Design and coding required
Number of Pages Required
1 page
Look and feel
Each slider illustrates characteristics of the customer's brand and the style your logo design should communicate.

```html
<!DOCTYPE html>
<html lang="en">
<head>
<meta charset="utf-8">
<title>Quorbelline – Digital Asset Management</title>
<link href="https://fonts.googleapis.com/css2?family=Roboto:wght@300;400;500;700&display=swap" rel="stylesheet">
<style>
:root{
  --navy:#1b2b8f;
  --navy-band:#13249a;
  --sky:#3ea3db;
  --heading:#23318e;
  --text:#777a80;
  --dark:#333;
  --light-bg:#f4f5f7;
  --footer:#1f1f1f;
  --white:#fff;
}
*{margin:0;padding:0;box-sizing:border-box}
html,body{width:1200px;height:2476px;overflow:hidden}
body{font-family:'Roboto',sans-serif;background:var(--white);color:var(--dark);position:relative}
section,header,footer{position:absolute;left:0;width:1200px}
.abs{position:absolute}

/* hero */
.hero{top:0;height:583px;overflow:hidden}
.hero-photo{position:absolute;inset:0;background:linear-gradient(135deg,#4b4f55 0%,#2c2f34 45%,#3d4148 70%,#24272b 100%)}
.hero-shade{position:absolute;inset:0;background:rgba(20,22,26,.35)}
.brand{left:86px;top:16px;display:flex;flex-direction:column;align-items:center;color:var(--white)}
.brand-mark{width:86px;height:86px;border-radius:50%;background:var(--white)}
.brand-name{margin-top:8px;font-size:14px;letter-spacing:1px}
.nav{top:56px;left:420px;font-size:12px;font-weight:500;color:var(--white)}
.nav a{color:inherit;text-decoration:none;position:absolute;white-space:nowrap}
.search{left:1066px;top:40px;width:48px;height:48px;border:1.5px solid var(--white);border-radius:50%;display:flex;align-items:center;justify-content:center}
.arrow{top:264px;width:52px;height:52px;border:2.5px solid var(--white);border-radius:50%;display:flex;align-items:center;justify-content:center}
.hero-copy{top:232px;left:0;width:1200px;text-align:center;color:var(--white)}
.hero-copy h1{font-size:31px;font-weight:500;letter-spacing:.5px}
.hero-copy h2{font-size:31px;font-weight:300;color:var(--sky);margin-top:14px}
.hero-copy p{font-size:12px;line-height:23px;width:580px;margin:16px auto 0}
.btn{display:inline-flex;align-items:center;justify-content:center;color:var(--white);font-size:14px;font-weight:500;text-decoration:none}
.btn-sky{background:var(--sky);width:140px;height:42px;margin-top:36px}

/* welcome */
.welcome{top:583px;height:413px}
.welcome-photo{left:86px;top:48px;width:442px;height:313px;background:linear-gradient(160deg,#b9a98a 0%,#8f7d5c 45%,#6f7f6a 100%)}
.welcome-title{left:593px;top:64px;font-size:23px;font-weight:400;color:var(--heading)}
.welcome-text{left:593px;top:110px;width:450px;font-size:11.5px;line-height:25.6px;color:var(--text)}
.btn-navy{left:596px;top:290px;width:135px;height:47px;background:var(--navy);position:absolute}

/* team */
.team{top:996px;height:523px;background:var(--light-bg)}
.section-title{width:1200px;text-align:center;font-size:23px;font-weight:400;color:var(--heading)}
.team .section-title{top:34px}
.team-sub{top:76px;width:1200px;text-align:center;font-size:11.5px;color:var(--text)}
.member{top:126px;width:320px;text-align:center}
.avatar{width:167px;height:167px;border-radius:50%;margin:0 auto;border:4px solid var(--white);box-shadow:0 0 0 1px #ddd}
.member h3{margin-top:16px;font-size:16px;font-weight:500;color:#333}
.member .role{margin-top:8px;font-size:13px;color:var(--text)}
.member p.bio{margin-top:10px;font-size:11.5px;line-height:25px;color:var(--text);padding:0 20px}
.socials{display:flex;gap:8px;justify-content:center;margin-top:22px}
.socials span{width:34px;height:34px;border:1.5px solid #c8c8c8;border-radius:50%;display:flex;align-items:center;justify-content:center;font-size:8px;color:#999}

/* process */
.process{top:1519px;height:487px}
.process-title{left:84px;top:50px;font-size:26px;font-weight:400;color:var(--heading)}
.label{left:86px;font-size:12.5px;font-weight:700;color:var(--sky)}
.process-text{left:86px;top:124px;width:540px;font-size:11.5px;line-height:26.5px;color:var(--text)}
.profit-list{left:86px;top:252px;list-style:none;font-size:11.5px;color:var(--text)}
.profit-list li{height:29px;display:flex;align-items:center;gap:14px}
.process-visual{left:664px;top:38px;width:450px;height:416px;background:linear-gradient(180deg,#e9ecef 0%,#d7dbe0 70%,#eef0f2 100%)}

/* band */
.band{top:2006px;height:234px;background:var(--navy-band);text-align:center;color:var(--white)}
.band h2{margin-top:48px;font-size:18px;font-weight:500;letter-spacing:.3px}
.band h3{margin-top:12px;font-size:23px;font-weight:300;letter-spacing:.3px}
.btn-outline{width:269px;height:48px;border:1.5px solid var(--white);margin-top:28px;font-weight:400;font-size:14px}

/* footer */
.footer{top:2240px;height:236px;background:var(--footer);color:var(--white)}
.footer-social{top:35px;left:0;width:1200px;display:flex;justify-content:center;gap:15px}
.footer-social span{width:57px;height:57px;border:1.5px solid #cfcfcf;border-radius:50%;display:flex;align-items:center;justify-content:center;font-size:10px;font-weight:500;color:var(--white)}
.footer-rule{top:108px;left:86px;width:1028px;height:1px;background:#3a3a3a}
.footer-nav{top:134px;width:1200px;display:flex;justify-content:center;font-size:11.5px;color:#ddd}
.footer-nav a{color:inherit;text-decoration:none;padding:0 30px;border-left:1px solid #888;line-height:12px}
.footer-nav a:first-child{border-left:none}
.copyright{top:176px;width:1200px;text-align:center;font-size:11px;color:#ccc}
</style>
</head>
<body>

<header class="hero">
  <div class="hero-photo" role="img" aria-label="Dimmed photo of business people working at a desk with laptop and charts"></div>
  <div class="hero-shade"></div>

  <div class="brand abs">
    <div class="brand-mark"></div>
    <div class="brand-name">Quorbelline</div>
  </div>

  <nav class="nav abs">
    <a style="left:19px">HOME</a>
    <a style="left:119px">ABOUT US</a>
    <a style="left:242px">SERVICES</a>
    <a style="left:361px">NEWS</a>
    <a style="left:460px">TEAM</a>
    <a style="left:559px">CONTACT US</a>
  </nav>
  <div class="search abs">
    <svg width="14" height="14" viewBox="0 0 14 14"><circle cx="6" cy="6" r="4.3" fill="none" stroke="#fff" stroke-width="2"/><line x1="9.2" y1="9.2" x2="12.8" y2="12.8" stroke="#fff" stroke-width="2.2" stroke-linecap="round"/></svg>
  </div>

  <div class="arrow abs" style="left:24px">
    <svg width="16" height="20" viewBox="0 0 16 20"><polyline points="11,3 4,10 11,17" fill="none" stroke="#fff" stroke-width="3"/></svg>
  </div>
  <div class="arrow abs" style="left:1122px">
    <svg width="16" height="20" viewBox="0 0 16 20"><polyline points="5,3 12,10 5,17" fill="none" stroke="#fff" stroke-width="3"/></svg>
  </div>

  <div class="hero-copy abs">
    <h1>QUORBELLINE</h1>
    <h2>DIGITAL ASSET MANAGEMENT</h2>
    <p>Quorbelline enable companies and investors to facilities business operation in modern digital world, including asset management on hedge fund strategy model.</p>
    <a class="btn btn-sky">READ MORE</a>
  </div>
</header>

<section class="welcome">
  <div class="welcome-photo abs" role="img" aria-label="Photo of coin stacks and banknotes with a small chalkboard sign reading financial support"></div>
  <h2 class="welcome-title abs">WELCOME TO QUORBELLINE</h2>
  <p class="welcome-text abs">Quorbelline process and manages on hedge fund strategy models which invests in a diversified portfolio of blockchain tokens. Blockchain tokens are emerging which add a monetary incentive layer to p2p protocols and facilitate equity crowdfunding that anyone in the world can participate in. This means open source software developers can monetize their networks at the protocol level and users of the of the network. For this conditions, returns will go to holders of the tokens.</p>
  <a class="btn btn-navy">READ MORE</a>
</section>

<section class="team">
  <h2 class="section-title abs">EXECUTIVE TEAM</h2>
  <p class="team-sub abs">Blockchain tokens are emerging which add a monetary incentive layer to p2p protocols and facilitate equity</p>

  <div class="member abs" style="left:94px">
    <div class="avatar" style="background:linear-gradient(180deg,#6d6e72,#3b3c40)" role="img" aria-label="Portrait photo of the director"></div>
    <h3>Kittipan Wongsarat</h3>
    <div class="role">Director</div>
    <p class="bio">As a hedge fund manager. Wongsarat is the Chief Executive Officer of Harrowfield Capital an investment manager of Calloway...</p>
    <div class="socials"><span>Feed</span><span>Link</span></div>
  </div>

  <div class="member abs" style="left:438px">
    <div class="avatar" style="background:linear-gradient(180deg,#d9ddc8,#9aa3a6)" role="img" aria-label="Portrait photo of the technical advisor"></div>
    <h3>Natthawut Sornchai</h3>
    <div class="role">Technical advisor</div>
    <p class="bio">Sornchai has various experienced on cryptocurrency and blockchain technology. He created what was 4th most valuable cryptocurrency</p>
    <div class="socials"><span>Feed</span><span>Link</span></div>
  </div>

  <div class="member abs" style="left:783px">
    <div class="avatar" style="background:linear-gradient(180deg,#7a2e22,#4a1a14)" role="img" aria-label="Portrait photo of the marketing consultant"></div>
    <h3>Pakorn Leelawanich</h3>
    <div class="role">Marketing Consultant</div>
    <p class="bio">Leelawanich embeds a decade of experience in brand building, strategic planning, and marketing communication across the global...</p>
    <div class="socials"><span>Feed</span><span>Link</span></div>
  </div>
</section>

<section class="process">
  <h2 class="process-title abs">OUR PROCESS</h2>
  <div class="label abs" style="top:94px">HEDGE FUND MODEL</div>
  <p class="process-text abs">Quorbelline run on closed-end fund （CEF） model which offers its shares to investors and utilize the fund to speculate and invest in the innovative blockchain tokens. Quorbelline will charge an upfront annual operation fee 4% of the money raised during the ICO.</p>
  <div class="label abs" style="top:216px">NET PROFIT DISTRIBUTION</div>
  <ul class="profit-list abs">
    <li><svg width="12" height="10" viewBox="0 0 12 10"><polyline points="1,5 4.5,8.5 11,1.5" fill="none" stroke="#3ea3db" stroke-width="2.2"/></svg>50 % of net profit is distributed to investors</li>
    <li><svg width="12" height="10" viewBox="0 0 12 10"><polyline points="1,5 4.5,8.5 11,1.5" fill="none" stroke="#3ea3db" stroke-width="2.2"/></svg>0 – 5 % net profit &gt; 0% performance fee</li>
    <li><svg width="12" height="10" viewBox="0 0 12 10"><polyline points="1,5 4.5,8.5 11,1.5" fill="none" stroke="#3ea3db" stroke-width="2.2"/></svg>5 – 10% net profit &gt; 5% performance fee</li>
    <li><svg width="12" height="10" viewBox="0 0 12 10"><polyline points="1,5 4.5,8.5 11,1.5" fill="none" stroke="#3ea3db" stroke-width="2.2"/></svg>10-15 % net profit &gt; 13% performance fee</li>
    <li><svg width="12" height="10" viewBox="0 0 12 10"><polyline points="1,5 4.5,8.5 11,1.5" fill="none" stroke="#3ea3db" stroke-width="2.2"/></svg>&gt; 15% net profit &gt; 15% performance fee</li>
    <li><svg width="12" height="10" viewBox="0 0 12 10"><polyline points="1,5 4.5,8.5 11,1.5" fill="none" stroke="#3ea3db" stroke-width="2.2"/></svg>The remainder （50% minus performance fee, so at least 35%）is reinvested</li>
  </ul>
  <div class="process-visual abs" role="img" aria-label="Illustration of a desktop computer showing a business consultation graphic"></div>
</section>

<section class="band">
  <h2>QUORBELLINE IS EMPLOYING A MARKET NEUTRAL, LONG/SHORT EQUITY STRATEGY</h2>
  <h3>OUR SYSTEM MANAGES A DIVERSE PORTFOLIO &amp; USES</h3>
  <a class="btn btn-outline">CLICK HERE FOR MORE INFO</a>
</section>

<footer class="footer">
  <div class="footer-social abs">
    <span>Feed</span><span>Post</span><span>Circle</span><span>Link</span><span>Pics</span>
    <span><svg width="18" height="14" viewBox="0 0 18 14"><rect x="1" y="1" width="16" height="12" fill="none" stroke="#fff" stroke-width="1.6"/><polyline points="1,1 9,8 17,1" fill="none" stroke="#fff" stroke-width="1.6"/></svg></span>
  </div>
  <div class="footer-rule abs"></div>
  <nav class="footer-nav abs">
    <a>HOME</a><a>ABOUT US</a><a>SERVICES</a><a>NEWS</a><a>TEAM</a><a>CONTACT US</a>
  </nav>
  <p class="copyright abs">© Copyrights 2017 Quorbelline.All Rights Reserved.</p>
</footer>

</body>
</html>
```